Alapca breeding needs a website

Presentation of the farm, animals (stallions, mares, information about the animals, for sale) and possible later expansion with a webshop (alpaca wool products). We want to present our farm and the animals on the farm on this page. A mission why we are doing this. Furthermore, each animal should be shown with a picture and described. Later we want to sell our own products made from alpaca wool via a webshop. But we still need to grow a bit to do that.

Target Market(s)

Information about my alpaca breeding and the alpaca farm

Industry/Entity Type

Tierzucht

Number of Pages Required

1 page

Font styles to use
Sans Serif

Requirements
Must have
• Modern design that matches the logo
Nice to have
• Intuitive operation / Clear structure
Should not have
• No

```html
<!DOCTYPE html>
<html lang="en">
<head>
<meta charset="utf-8">
<title>Loma Alpacas</title>
<link href="https://fonts.googleapis.com/css2?family=Cinzel:wght@700&family=Roboto:wght@400;500;700&display=swap" rel="stylesheet">
<style>
:root{
  --navy:#0c2340;
  --green:#8cc63f;
  --grey-bg:#f4f4f4;
  --text:#555b63;
  --white:#ffffff;
}
*{margin:0;padding:0;box-sizing:border-box}
html,body{width:1200px;height:3692px;overflow:hidden}
body{position:relative;font-family:'Roboto',Arial,sans-serif;color:var(--text);background:var(--white)}
.abs{position:absolute}
.serif{font-family:'Cinzel',Georgia,serif;font-weight:700;color:var(--navy)}
.top-line{left:0;top:0;width:1200px;height:4px;background:var(--green)}
.contact-pill{left:530px;top:3px;width:525px;height:38px;background:var(--green);border-radius:19px;display:flex;align-items:center;gap:40px;padding-left:30px;color:#fff;font-size:14px}
.contact-pill span{display:flex;align-items:center;gap:8px}
.ico{width:24px;height:24px;border-radius:50%;background:var(--navy);display:inline-flex;align-items:center;justify-content:center}
.brand{left:143px;top:42px;display:flex;align-items:center;gap:8px;font-weight:700;font-size:22px;color:var(--navy);letter-spacing:1px}
.brand i{width:14px;height:14px;border-radius:50%;background:var(--green);display:block}
.nav{top:70px;left:0;font-size:14px;color:#333}
.nav a{position:absolute;color:#333;text-decoration:none;white-space:nowrap}
.nav a.active{color:var(--green)}
.nav a.active::after{content:"";position:absolute;left:0;right:0;top:24px;height:3px;background:var(--green)}
.cart{left:940px;top:64px;display:flex;align-items:center;gap:14px;font-size:14px;color:#333}
.cart .c{width:30px;height:30px;border-radius:50%;background:#fff;box-shadow:0 2px 8px rgba(0,0,0,.15);display:flex;align-items:center;justify-content:center}
.hero{left:0;top:115px;width:1200px;height:680px;background:linear-gradient(120deg,#5c8a3a 0%,#7fae4d 40%,#b8c7a5 65%,#6e9a3f 100%);overflow:hidden}
.hero h1{position:absolute;left:143px;top:160px;font-size:68px;line-height:72px;color:#fff}
.hero p{position:absolute;left:142px;top:318px;font-size:17px;line-height:24px;color:#fff;width:360px}
.btn{display:inline-flex;align-items:center;justify-content:center;background:var(--green);color:#fff;font-weight:700;text-transform:uppercase;border-radius:22px;box-shadow:0 4px 10px rgba(0,0,0,.15)}
.hero .btn{position:absolute;left:142px;top:384px;width:166px;height:43px;font-size:15px}
.side-tab{left:1157px;top:350px;width:43px;height:166px;background:var(--green);border-radius:22px 0 0 22px;color:#fff;font-weight:700;font-size:14px;writing-mode:vertical-rl;display:flex;align-items:center;justify-content:center;letter-spacing:1px}
.about-art{left:129px;top:843px;width:466px;height:447px;border-radius:50%;background:radial-gradient(circle at 50% 40%,#d9ecc2 0%,#a6cf74 45%,#1a3455 100%)}
.h2{font-size:37px;letter-spacing:1px}
.underline{height:3px;background:var(--green);width:104px}
.about-title{left:628px;top:856px}
.about-ul{left:630px;top:907px}
.about-text{left:631px;top:928px;width:426px;font-size:14px;line-height:20px;text-align:justify}
.about-text p+p{margin-top:20px}
.about .btn{position:absolute;left:628px;top:1244px;width:166px;height:43px;font-size:15px;gap:6px}
.sale{left:0;top:1405px;width:1200px;height:644px;background:var(--grey-bg)}
.center-title{left:0;width:1200px;text-align:center}
.center-ul{left:548px}
.animal{width:290px;text-align:center}
.animal .ring{width:284px;height:284px;margin:0 auto;border-radius:50%;border:10px solid var(--green);padding:0;position:relative}
.animal .ring.bottom{border-top-color:transparent;border-right-color:transparent;transform:rotate(-45deg)}
.animal .ring.top{border-bottom-color:transparent;border-left-color:transparent;transform:rotate(-45deg)}
.animal .photo{position:absolute;inset:0;border-radius:50%;transform:rotate(45deg)}
.animal h3{font-size:18px;color:var(--navy);font-weight:700;margin-top:17px}
.animal p{font-size:14px;line-height:21px;margin-top:8px}
.wool{left:0;top:2049px;width:1200px;height:591px;background:var(--navy)}
.green-box{left:110px;top:2288px;width:362px;height:350px;background:var(--green);border-radius:36px}
.jump-photo{left:150px;top:2194px;width:237px;height:416px;border-radius:40px 40px 20px 20px;background:linear-gradient(180deg,#d2a679,#a5713f)}
.card{top:2288px;width:191px;height:215px;background:#fff;border-radius:4px;padding:11px}
.card .img{height:161px;border-radius:4px}
.card h4{text-align:center;font-size:15px;font-weight:500;color:var(--navy);margin-top:12px}
.arrow{top:2555px;width:34px;height:34px;border:2px solid #fff;border-radius:50%;display:flex;align-items:center;justify-content:center}
.review{top:2824px;width:433px;height:266px;background:var(--grey-bg);border-radius:6px;padding:38px 29px 0}
.review p{font-size:13.5px;line-height:20px}
.reviewer{display:flex;align-items:center;gap:13px;margin-top:22px;margin-left:4px}
.avatar{width:66px;height:66px;border-radius:50%;background:linear-gradient(180deg,#c9c3bd,#6f6a66)}
.reviewer b{display:block;font-size:20px;color:var(--navy);font-weight:500}
.reviewer small{font-size:13px}
.quote{position:absolute;right:25px;bottom:-20px;font-family:Georgia,serif;font-size:74px;font-weight:700;color:var(--green);line-height:1}
.dot{top:3120px;width:12px;height:12px;border-radius:50%;border:1.5px solid #555}
.dot.on{background:var(--green);border-color:var(--green)}
.footer{left:0;top:3190px;width:1200px;height:502px}
.f-col{top:3382px;color:#fff}
.f-col h3{font-size:27px;font-weight:500;margin-bottom:22px}
.f-col li{list-style:none;font-size:14px;height:24px;display:flex;align-items:center;gap:14px}
.f-col .info{display:flex;gap:14px;font-size:14px;line-height:24px;margin-bottom:24px}
.f-col .info svg{flex:none;margin-top:5px}
.email{width:311px;height:37px;background:#fff;border-radius:4px;font-size:14px;color:#666;padding:10px 15px}
.f-col .btn{width:149px;height:37px;font-size:16px;margin-top:14px;margin-left:3px}
.copy{left:0;top:3642px;width:1200px;text-align:center;color:#fff;font-size:14px}
</style>
</head>
<body>
<div class="abs top-line"></div>
<div class="abs contact-pill">
  <span><i class="ico"><svg width="12" height="12" viewBox="0 0 24 24"><path fill="#fff" d="M6.6 10.8a15 15 0 0 0 6.6 6.6l2.2-2.2c.3-.3.7-.4 1-.2 1.1.4 2.3.6 3.6.6.6 0 1 .4 1 1V20c0 .6-.4 1-1 1A17 17 0 0 1 3 4c0-.6.4-1 1-1h3.5c.6 0 1 .4 1 1 0 1.3.2 2.5.6 3.6.1.3 0 .7-.2 1z"/></svg></i>Call Us : +1 888 888 8888</span>
  <span><i class="ico"><svg width="12" height="10" viewBox="0 0 24 18"><path fill="#fff" d="M0 0h24v2L12 10 0 2zM0 5l12 8 12-8v13H0z"/></svg></i>Mail Us : info@companyname.com</span>
</div>
<div class="abs brand"><i></i>LOMA ALPACAS</div>
<nav class="abs nav">
  <a class="active" style="left:437px">Home</a>
  <a style="left:500px">About</a>
  <a style="left:563px">Services</a>
  <a style="left:641px">Blog</a>
  <a style="left:695px">Reviews</a>
  <a style="left:773px">Contact</a>
  <svg class="abs" style="left:879px;top:2px" width="14" height="14" viewBox="0 0 24 24"><circle cx="10" cy="10" r="7" fill="none" stroke="#333" stroke-width="3"/><path d="M15 15l7 7" stroke="#333" stroke-width="3"/></svg>
</nav>
<div class="abs cart"><span class="c"><svg width="14" height="12" viewBox="0 0 24 20"><path fill="#8cc63f" d="M0 0h4l1 3h19l-3 9H7l-1 2h16v2H3l2-4L2 2H0z"/><circle cx="7" cy="18" r="2" fill="#8cc63f"/><circle cx="19" cy="18" r="2" fill="#8cc63f"/></svg></span>My Cart :$0.00</div>

<section class="abs hero" role="img" aria-label="Photo of a white alpaca standing in a green meadow">
  <h1 class="serif" style="color:#fff">LOMA<br>ALPACAS</h1>
  <p>Lorem ipsum dolor sit amet, consectetur adipis cing elit, sed do eiusmod tempor</p>
  <span class="btn">Get Started</span>
  <svg class="abs" style="left:0;top:0" width="1200" height="680" viewBox="0 115 1200 680">
    <path d="M0 795 L0 792 Q600 694 1200 792 L1200 795Z" fill="#fff"/>
    <path d="M122 780 Q600 668 1075 780 Q600 706 122 780Z" fill="#0c2340"/>
    <circle cx="600" cy="721" r="31" fill="#fff"/>
    <path d="M600 709v22M592 723l8 8 8-8" stroke="#0c2340" stroke-width="2.5" fill="none"/>
  </svg>
</section>
<div class="abs side-tab">CONTACT US</div>

<section class="about">
  <div class="abs about-art" role="img" aria-label="Illustration of two alpacas beneath a leafy tree"></div>
  <h2 class="abs serif h2 about-title">ABOUT US</h2>
  <div class="abs underline about-ul"></div>
  <div class="abs about-text">
    <p>Lorem ipsum dolor sit amet, consectetur adipiscing elit, sed do eiusmod tempor incididunt ut labore et dolore magna aliqua. Ut enim ad minim veniam, quis nostrud exercitation ullamco laboris nisi ut aliquip ex ea commodo consequat. Duis aute irure dolor in reprehenderit in voluptate velit esse cillum dolore eu fugiat nulla pariatur. Excepteur sint occaecat cupidatat non proident, sunt in culpa qui officia deserunt mollit anim id est laborum.</p>
    <p>Lorem ipsum dolor sit amet, consectetur adipiscing elit, sed do eiusmod tempor incididunt ut labore et dolore magna aliqua. Ut enim ad minim veniam, quis nostrud exercitation ullamco laboris nisi ut aliquip ex ea commodo consequat. Duis aute irure dolor in reprehenderit in voluptate velit esse cillum dolore eu fugiat nulla pariatur. Excepteur sint occaecat cupidatat non proident, sunt in culpa qui officia deserunt mollit anim id est laborum.</p>
  </div>
  <span class="btn">Read More <svg width="14" height="14" viewBox="0 0 24 24"><circle cx="12" cy="12" r="11" fill="#fff"/><path d="M10 7l5 5-5 5" stroke="#8cc63f" stroke-width="3" fill="none"/></svg></span>
</section>

<section class="abs sale"></section>
<h2 class="abs serif h2 center-title" style="top:1508px">SALE FOR ANIMAL</h2>
<div class="abs underline center-ul" style="top:1561px"></div>
<div class="abs animal" style="left:130px;top:1589px">
  <div class="ring bottom"><div class="photo" role="img" aria-label="Photo of a brown stallion" style="background:linear-gradient(160deg,#9aa0a6,#5a3a22 60%,#3a2414)"></div></div>
  <h3>Stallions</h3><p>Lorem ipsum dolor sit amet, consec<br>tetur adipiscing elit</p>
</div>
<div class="abs animal" style="left:454px;top:1589px">
  <div class="ring top"><div class="photo" role="img" aria-label="Photo of a chestnut mare" style="background:linear-gradient(180deg,#a9c4e6,#b9652f 55%,#8a4a20)"></div></div>
  <h3>Mares</h3><p>Lorem ipsum dolor sit amet, consec<br>tetur adipiscing elit</p>
</div>
<div class="abs animal" style="left:778px;top:1589px">
  <div class="ring bottom"><div class="photo" role="img" aria-label="Photo of a white alpaca on a pasture" style="background:linear-gradient(180deg,#dfe6ee,#eeeae0 45%,#7fa54a)"></div></div>
  <h3>Alpaca</h3><p>Lorem ipsum dolor sit amet, consec<br>tetur adipiscing elit</p>
</div>

<section class="abs wool"></section>
<h2 class="abs serif h2 center-title" style="top:2150px;color:#fff">ALPACA WOOL PRODUCTS</h2>
<div class="abs underline center-ul" style="top:2203px"></div>
<div class="abs green-box"></div>
<div class="abs jump-photo" role="img" aria-label="Photo of a leaping brown alpaca"></div>
<div class="abs card" style="left:443px"><div class="img" role="img" aria-label="Skeins of natural alpaca yarn" style="background:linear-gradient(160deg,#7a5a45,#e8e2d8)"></div><h4>Lorem ipsum dolor</h4></div>
<div class="abs card" style="left:654px"><div class="img" role="img" aria-label="Folded alpaca wool blanket" style="background:linear-gradient(160deg,#4a2a26,#efece6 40%,#d8d2c8)"></div><h4>Lorem ipsum dolor</h4></div>
<div class="abs card" style="left:866px"><div class="img" role="img" aria-label="Brown and white alpaca wool" style="background:linear-gradient(90deg,#9a5a30,#e5dcd0 60%,#f5f2ec)"></div><h4>Lorem ipsum dolor</h4></div>
<div class="abs arrow" style="left:981px"><svg width="10" height="12" viewBox="0 0 10 12"><path d="M7 1L2 6l5 5" stroke="#fff" stroke-width="2" fill="none"/></svg></div>
<div class="abs arrow" style="left:1021px"><svg width="10" height="12" viewBox="0 0 10 12"><path d="M3 1l5 5-5 5" stroke="#fff" stroke-width="2" fill="none"/></svg></div>

<h2 class="abs serif h2 center-title" style="top:2731px">CLIENT REVIEWS</h2>
<div class="abs underline center-ul" style="top:2784px"></div>
<div class="abs review" style="left:143px">
  <p>Lorem ipsum dolor sit amet, consectetur adipiscing elit, sed do eiusmod tempor incididunt ut labore et dolore magna aliqua. Ut enim ad minim veniam, quis nostrud exercitation laboris nisi ut aliquip ex ea commodo consequat.</p>
  <div class="reviewer"><div class="avatar" role="img" aria-label="Client portrait"></div><div><b>John Doe</b><small>Company name</small></div></div>
  <span class="quote">&ldquo;</span>
</div>
<div class="abs review" style="left:624px">
  <p>Lorem ipsum dolor sit amet, consectetur adipiscing elit, sed do eiusmod tempor incididunt ut labore et dolore magna aliqua. Ut enim ad minim veniam, quis nostrud exercitation laboris nisi ut aliquip ex ea commodo consequat.</p>
  <div class="reviewer"><div class="avatar" role="img" aria-label="Client portrait"></div><div><b>John Doe</b><small>Company name</small></div></div>
  <span class="quote">&ldquo;</span>
</div>
<span class="abs dot" style="left:565px"></span>
<span class="abs dot on" style="left:583px"></span>
<span class="abs dot" style="left:602px"></span>
<span class="abs dot" style="left:621px"></span>

<footer class="abs footer">
  <svg width="1200" height="502" viewBox="0 3190 1200 502">
    <rect x="0" y="3190" width="1200" height="502" fill="#0c2340"/>
    <path d="M0 3190 L1200 3190 L1200 3200 Q600 3370 0 3200Z" fill="#fff"/>
    <path d="M122 3215 Q600 3340 1075 3215 Q600 3305 122 3215Z" fill="#8cc63f"/>
  </svg>
</footer>
<div class="abs f-col" style="left:179px">
  <h3>Quick Links</h3>
  <ul>
    <li><span>&raquo;</span>Home</li><li><span>&raquo;</span>About Us</li><li><span>&raquo;</span>Services</li>
    <li><span>&raquo;</span>Blog</li><li><span>&raquo;</span>Reviews</li><li><span>&raquo;</span>Contact</li>
  </ul>
</div>
<div class="abs f-col" style="left:428px">
  <h3>Contact Us</h3>
  <div class="info"><svg width="9" height="13" viewBox="0 0 12 18"><path fill="#8cc63f" d="M6 0a6 6 0 0 1 6 6c0 4-6 12-6 12S0 10 0 6a6 6 0 0 1 6-6zm0 3a3 3 0 1 0 0 6 3 3 0 0 0 0-6z"/></svg><span>123, Lorem ipsum dolor sit<br>amet, conse</span></div>
  <div class="info"><svg width="11" height="11" viewBox="0 0 24 24"><path fill="#8cc63f" d="M6.6 10.8a15 15 0 0 0 6.6 6.6l2.2-2.2c.3-.3.7-.4 1-.2 1.1.4 2.3.6 3.6.6.6 0 1 .4 1 1V20c0 .6-.4 1-1 1A17 17 0 0 1 3 4c0-.6.4-1 1-1h3.5c.6 0 1 .4 1 1 0 1.3.2 2.5.6 3.6.1.3 0 .7-.2 1z"/></svg><span>+1 888 888 8888</span></div>
  <div class="info"><svg width="12" height="10" viewBox="0 0 24 18"><path fill="#8cc63f" d="M0 0h24v2L12 10 0 2zM0 5l12 8 12-8v13H0z"/></svg><span>info@companyname.com</span></div>
</div>
<div class="abs f-col" style="left:708px">
  <h3>Subscribe toNewsletter</h3>
  <div class="email">Email address</div>
  <span class="btn">Subscribe</span>
</div>
<div class="abs copy">&copy; Copyrights 2024 | All Rights Reserved</div>
</body>
</html>
```